The most modern business card ever !!!

Our company call “Vendalo”. Vendalo is a technology company specialized in cruises solutions. Out main product is a platform to reserve cruises. This is a revolutionary platform that make easier to travel agencies and final users to reserve cruises across dozen companies like tibba, wernu, hpv, dgb, etc..We are a “start up”, with a young team of developers and we want to transmit it.. For it, we want something different, a modern business card that represent cruises and technology.. When someone receive this card, this person should say: wowww this is different… this is modern… this is a cruise related company..
- diferent, modern
- traditions business card

```html
<!DOCTYPE html>
<html lang="en">
<head>
<meta charset="utf-8">
<title>Vendalo — Business Card</title>
<link rel="stylesheet" href="https://fonts.googleapis.com/css2?family=Open+Sans:wght@400;600&family=Crimson+Text&display=swap">
<style>
  :root {
    --backdrop: #a3a3a3;
    --card: #ffffff;
    --ink: #1b1b1b;
    --accent: #2ea9dd;
    --accent-dark: #1f8fc0;
    --shadow: rgba(0, 0, 0, 0.28);
  }
  * { box-sizing: border-box; margin: 0; padding: 0; }
  html, body { width: 1200px; height: 867px; overflow: hidden; }
  body {
    background: var(--backdrop);
    font-family: "Open Sans", sans-serif;
    color: var(--ink);
    position: relative;
  }
  .card {
    position: absolute;
    width: 300px;
    height: 300px;
    background: var(--card);
    box-shadow: 4px 6px 14px var(--shadow);
  }
  .chevron {
    position: absolute;
    width: 100px;
    height: 300px;
    filter: drop-shadow(3px 4px 6px var(--shadow));
  }
  .chevron polygon { fill: var(--accent); }

  .card--back-a { left: 250px; top: 90px; }
  .chevron--back-a { left: 150px; top: 90px; }

  .card--back-b { left: 700px; top: 90px; }
  .chevron--back-b { left: 700px; top: 90px; }

  .card--front-a { left: 150px; top: 480px; }
  .chevron--front-a { left: 460px; top: 480px; }

  .card--front-b { left: 700px; top: 480px; }
  .chevron--front-b { left: 900px; top: 480px; }

  .contact {
    position: absolute;
    right: 24px;
    top: 58px;
    text-align: right;
  }
  .contact__name {
    font-size: 17px;
    font-weight: 400;
    letter-spacing: 0.5px;
  }
  .contact__title {
    font-family: "Crimson Text", serif;
    font-size: 13px;
    color: var(--accent);
    margin-top: 1px;
  }
  .contact__rule {
    width: 42px;
    height: 2px;
    background: var(--accent);
    margin: 8px 0 24px auto;
  }
  .contact__line {
    display: flex;
    justify-content: flex-end;
    align-items: center;
    gap: 8px;
    font-size: 12px;
    line-height: 22px;
  }
  .contact__icon { width: 11px; height: 11px; flex: none; }
  .contact__icon path, .contact__icon circle, .contact__icon rect { fill: none; stroke: var(--accent); stroke-width: 1.6; }
  .contact__icon .solid { fill: var(--accent); stroke: none; }

  .brand {
    position: absolute;
    top: 50%;
    transform: translateY(-50%);
    font-size: 24px;
    font-weight: 600;
    letter-spacing: 0.5px;
    color: var(--ink);
  }
  .card--front-a .brand { left: 22px; }
  .card--front-b .brand { left: 22px; }
</style>
</head>
<body>

  <!-- Back, fold-out pointing right -->
  <svg class="chevron chevron--back-a" viewBox="0 0 100 300" preserveAspectRatio="none" aria-hidden="true">
    <polygon points="0,0 38,0 100,150 38,300 0,300 62,150"/>
  </svg>
  <section class="card card--back-a">
    <div class="contact">
      <div class="contact__name">YOUR NAME</div>
      <div class="contact__title">Job title</div>
      <div class="contact__rule"></div>
      <div class="contact__line">000 000 0000
        <svg class="contact__icon" viewBox="0 0 12 12"><path class="solid" d="M2 1h3l1 3-2 1c1 2 2 3 3 3l1-2 3 1v3c0 1-1 1-1 1C5 11 1 7 1 2c0 0 0-1 1-1z"/></svg>
      </div>
      <div class="contact__line">youremail@xyz.com
        <svg class="contact__icon" viewBox="0 0 12 12"><rect x="1" y="2.5" width="10" height="7"/><path d="M1 2.5l5 4 5-4"/></svg>
      </div>
      <div class="contact__line">www.yourwebsite.com
        <svg class="contact__icon" viewBox="0 0 12 12"><circle cx="6" cy="6" r="5"/><path d="M1 6h10M6 1c-3 3-3 7 0 10M6 1c3 3 3 7 0 10"/></svg>
      </div>
    </div>
  </section>

  <!-- Back, fold-in pointing left -->
  <section class="card card--back-b">
    <div class="contact">
      <div class="contact__name">YOUR NAME</div>
      <div class="contact__title">Job title</div>
      <div class="contact__rule"></div>
      <div class="contact__line">000 000 0000
        <svg class="contact__icon" viewBox="0 0 12 12"><path class="solid" d="M2 1h3l1 3-2 1c1 2 2 3 3 3l1-2 3 1v3c0 1-1 1-1 1C5 11 1 7 1 2c0 0 0-1 1-1z"/></svg>
      </div>
      <div class="contact__line">youremail@xyz.com
        <svg class="contact__icon" viewBox="0 0 12 12"><rect x="1" y="2.5" width="10" height="7"/><path d="M1 2.5l5 4 5-4"/></svg>
      </div>
      <div class="contact__line">www.yourwebsite.com
        <svg class="contact__icon" viewBox="0 0 12 12"><circle cx="6" cy="6" r="5"/><path d="M1 6h10M6 1c-3 3-3 7 0 10M6 1c3 3 3 7 0 10"/></svg>
      </div>
    </div>
  </section>
  <svg class="chevron chevron--back-b" viewBox="0 0 100 300" preserveAspectRatio="none" aria-hidden="true">
    <polygon points="62,0 100,0 38,150 100,300 62,300 0,150"/>
  </svg>

  <!-- Front, fold-out pointing left -->
  <section class="card card--front-a">
    <div class="brand">Vendalo</div>
  </section>
  <svg class="chevron chevron--front-a" viewBox="0 0 100 300" preserveAspectRatio="none" aria-hidden="true">
    <polygon points="62,0 100,0 38,150 100,300 62,300 0,150"/>
  </svg>

  <!-- Front, fold-in pointing right -->
  <section class="card card--front-b">
    <div class="brand">Vendalo</div>
  </section>
  <svg class="chevron chevron--front-b" viewBox="0 0 100 300" preserveAspectRatio="none" aria-hidden="true">
    <polygon points="0,0 38,0 100,150 38,300 0,300 62,150"/>
  </svg>

</body>
</html>
```